Stationery for use with Ninefold Ridge reports

I would like to get a stationery design that my firm -- Ninefold Ridge Advisory -- will use as a format for reports that we send our clients. I am specifically looking for a design for use on a piece of paper or letterhead -- not business cards or envelopes.

We are an Africa based US risk intelligence and strategy firm that works with multinational corporations operating in West Africa. Our initial thinking is that we would like a color scheme consistent with our existing logo -- however we are open to other color schemes.

Also, we would like to see at least two separate versions: one with our company name and logo, the other without name and logo.

We also would like font recommendations for the stationary design.

The final design should communicate discreet professionalism and a modern approach, but it should not overshadow the words and information printed on the stationery.

Target Market(s)

Multinational corporations that currently use our products.

Font styles to use
Serif
Sans Serif

Requirements
Must have
• Sense of discreet professionalism that will not overshadow the content we put onto the stationery format.
• We would like to see designs with and without our company name/logo.
• Please suggest fonts that would work with the stationery.
Nice to have
• Ideally colors consistent with out existing logo, though we are open to and even encourage other ideas.
Should not have
• No need for business cards or envelopes.

```html
<!DOCTYPE html>
<html lang="en">
<head>
<meta charset="utf-8">
<title>Ninefold Ridge Advisory — Letterhead</title>
<link href="https://fonts.googleapis.com/css2?family=Open+Sans:wght@400;700&family=Roboto:wght@400&display=swap" rel="stylesheet">
<style>
  :root {
    --backdrop: #d0ecf4;
    --paper: #ffffff;
    --navy: #1f3a4f;
    --ink: #555b60;
    --contact-ink: #3c4b58;
    --ochre: #b07a2c;
    --sky: #acd5ec;
    --signature-tone: #e9eaec;
  }
  * { margin: 0; padding: 0; box-sizing: border-box; }
  html, body {
    width: 1200px; height: 1200px; overflow: hidden;
    background: var(--backdrop);
  }
  .page {
    position: absolute; left: 242px; top: 94px;
    width: 716px; height: 1012px;
    background: var(--paper);
    overflow: hidden;
    font-family: "Open Sans", sans-serif;
  }
  .brand {
    position: absolute; left: 38px; top: 114px;
    display: flex; align-items: flex-end;
    width: 640px;
  }
  .brand-rule-short { width: 16px; height: 2px; background: var(--navy); margin-bottom: 6px; margin-right: 6px; }
  .brand-name {
    font-family: "Open Sans", sans-serif; font-weight: 700;
    font-size: 21px; letter-spacing: 0.5px; color: var(--navy);
    white-space: nowrap; line-height: 1;
  }
  .brand-rule-long { flex: 1; height: 2px; background: var(--navy); margin-bottom: 6px; margin-left: 8px; }
  .contact {
    position: absolute; left: 524px; top: 55px;
    font-family: "Roboto", sans-serif; font-size: 12px;
    color: var(--contact-ink); line-height: 14px;
  }
  .contact-line { display: flex; align-items: center; gap: 5px; }
  .contact-address { margin-bottom: 8px; }
  .contact-line + .contact-line { margin-top: 1px; }
  .date {
    position: absolute; left: 72px; top: 302px;
    font-size: 12.5px; color: var(--ink);
  }
  .letter-body {
    position: absolute; left: 72px; top: 362px;
    font-size: 12.5px; color: var(--ink);
  }
  .letter-body p { margin-bottom: 5px; }
  .letter-body span { display: block; line-height: 26px; white-space: nowrap; }
  .signature-mark {
    position: absolute; left: 498px; top: 703px;
    width: 146px; height: 44px; border-radius: 4px;
    background: var(--signature-tone);
  }
  .signatory {
    position: absolute; left: 503px; top: 746px;
    font-size: 12.5px; color: var(--ink); line-height: 14px;
  }
  .footer-art { position: absolute; left: 0; top: 980px; }
  .website {
    position: absolute; left: 505px; top: 987px;
    font-family: "Roboto", sans-serif; font-size: 16px; color: #ffffff;
  }
</style>
</head>
<body>
  <main class="page">
    <header>
      <div class="brand">
        <div class="brand-rule-short"></div>
        <div class="brand-name">NINEFOLD RIDGE ADVISORY</div>
        <div class="brand-rule-long"></div>
      </div>
      <address class="contact" style="font-style:normal">
        <div class="contact-address">Your address, city<br>state, ZIP 0000</div>
        <div class="contact-line">
          <svg width="11" height="11" viewBox="0 0 24 24" aria-hidden="true"><path fill="#b07a2c" d="M6.6 10.8a15.1 15.1 0 0 0 6.6 6.6l2.2-2.2a1 1 0 0 1 1-.25 11.4 11.4 0 0 0 3.6.57 1 1 0 0 1 1 1V20a1 1 0 0 1-1 1A17 17 0 0 1 3 4a1 1 0 0 1 1-1h3.5a1 1 0 0 1 1 1c0 1.25.2 2.45.57 3.57a1 1 0 0 1-.25 1z"/></svg>
          <span>123-456-2100</span>
        </div>
        <div class="contact-line">
          <svg width="11" height="11" viewBox="0 0 24 24" aria-hidden="true"><path fill="#b07a2c" d="M2 5h20v14H2z"/><path fill="none" stroke="#fff" stroke-width="2" d="M2 5l10 8 10-8"/></svg>
          <span>youremail@ninefoldridge.com</span>
        </div>
      </address>
    </header>

    <div class="date">Date, 10 September, 2020</div>

    <section class="letter-body">
      <p>
        <span>This is a sample letter that has been placed to demonstrate typing remat (Your Company). letterhead</span>
        <span>design. When positioned properly, it will serve to work in harmony with all other elements letterhead.</span>
        <span>This letterhead design is meant to project an image</span>
      </p>
      <p>
        <span>This letterhead design is meant project an image of professionalism reliability. By using simple aligen</span>
        <span>we have created a very spacious feeling. The simplicity suggest &nbsp;rengththe spaciousnes contributes h</span>
        <span>aesthetics the layout. These basic qualities along with the (Your Company)</span>
      </p>
      <p>
        <span>look and helps reinforce the (Your Company) brand. letterhead design is meant to project an image p</span>
        <span>design. When positioned properly, it will serve to work in harmony all the other elements letterhead.</span>
        <span>sionalism and reliability.</span>
      </p>
      <p>
        <span>This letterhead design is based on the (Form of your logo) form (Your Company) logo. Each stationery</span>
        <span>we have created a very spacious feeling. The simplicity suggests strength the spaciousnes contribute</span>
        <span>part of the (Form of your logo).</span>
      </p>
    </section>

    <div class="signature-mark" role="img" aria-label="Handwritten signature of Daniel Harrow"></div>
    <div class="signatory">Daniel Harrow<br>Manager</div>

    <svg class="footer-art" width="716" height="32" viewBox="0 0 716 32" aria-hidden="true">
      <rect x="0" y="9" width="470" height="5" fill="var(--sky)"/>
      <rect x="0" y="22" width="716" height="10" fill="var(--ochre)"/>
      <path d="M450 32 C470 32 470 3 495 3 L716 3 L716 32 Z" fill="var(--ochre)"/>
    </svg>
    <div class="website">www.yourwebsite.com</div>
  </main>
</body>
</html>
```